Ordnerdesign für Experte für Versicherungs - und Haftungsfragen im Etiketten - und Verpackungsdruck
Super engagiert und vor allen Dingen sehr geduldig , hat meine Erwartungen übertroffen
Zielgruppe
Ich bin Konrad Wilmeth Experte für Versicherungs - und Haftungsfragen im Etiketten - und Verpackungsdruck (meine CI Farben sind orange /schwarz ) Meine Company und das Produkt ist die tervalon und der tervalon Schutzbrief für Druckerereien (schwarz/gelb)
Aufgabenstellung
Gesucht wird für mein/unser Projekt : Ordnerdesign PLUS Register eines Notfallhandbuchs für Unternehmer . Es gibt zwei Produktlinien - zu beiden ist jeweils der Farbfächer /Broschüre beigefügt : Entweder der Notfallordner soll unter ' Konrad Wilmeth Experte für Haftungsfragen .. ( Orange Schwarz oder die Farben meiner Company ( tervalon Schwarz - gelb ) siehe Broschüre angelegt werden. freie Hand , was also besser passt .

```html
<!DOCTYPE html>
<html lang="de">
<head>
<meta charset="utf-8">
<title>Notfallhandbuch – Ordner und Register</title>
<link rel="stylesheet" href="https://fonts.googleapis.com/css2?family=Lexend:wght@300;400;500;600&display=swap">
<style>
  :root {
    --orange: #d94f2b;
    --orange-deep: #c9401f;
    --pattern: #d5381f;
    --yellow: #f5c842;
    --white: #ffffff;
    --ink: #1a1a1a;
    --paper: #ffffff;
  }
  * { box-sizing: border-box; margin: 0; padding: 0; }
  html, body { width: 1199px; height: 1200px; overflow: hidden; background: var(--paper); }
  body { position: relative; font-family: "Lexend", sans-serif; color: var(--white); }

  .panel {
    position: absolute;
    width: 498px; height: 521px;
    background: var(--orange);
    overflow: hidden;
    box-shadow: 0 4px 10px rgba(0,0,0,0.25);
  }
  .panel--cover { left: 79px; top: 41px; }
  .panel--overview { left: 638px; top: 41px; }
  .panel--chapter4 { left: 79px; top: 639px; }
  .panel--chapter9 { left: 638px; top: 639px; }

  .brand {
    position: absolute; top: 0;
    background: var(--white);
    color: var(--ink);
    display: flex; align-items: center; justify-content: center;
    font-weight: 500;
    letter-spacing: -0.01em;
  }
  .brand--large { left: 47px; width: 156px; height: 69px; font-size: 24px; }
  .brand--small { left: 56px; width: 99px; height: 44px; font-size: 15px; }

  .cover-pattern {
    position: absolute; inset: 0;
    background: linear-gradient(135deg, rgba(213,56,31,0) 35%, rgba(213,56,31,0.55) 70%, rgba(213,56,31,0.3) 100%);
  }
  .signature {
    position: absolute;
    background: linear-gradient(90deg, rgba(26,26,26,0.55), rgba(26,26,26,0.25));
    border-radius: 40% 50% 40% 50%;
  }
  .signature--cover { left: 46px; top: 155px; width: 254px; height: 62px; }
  .signature--footer { width: 68px; height: 20px; top: 463px; }

  .cover-title {
    position: absolute; left: 44px; top: 218px;
    font-size: 62px; font-weight: 600; line-height: 68px;
    letter-spacing: -0.01em;
  }
  .author-vertical {
    position: absolute; left: 52px; top: 490px;
    transform: rotate(-90deg); transform-origin: left top;
    font-size: 7px; color: var(--ink); white-space: nowrap;
  }
  .badge {
    position: absolute; left: 362px; top: 404px;
    width: 84px; height: 84px; border-radius: 50%;
    background: var(--yellow); color: var(--ink);
    display: flex; flex-direction: column; justify-content: center;
    padding-left: 11px;
    box-shadow: 0 3px 8px rgba(0,0,0,0.25);
  }
  .badge__title { font-size: 8.5px; font-weight: 600; line-height: 11px; letter-spacing: 0.03em; }
  .badge__sub { font-size: 5.5px; font-weight: 500; margin-top: 3px; letter-spacing: 0.03em; }

  .contents-label {
    position: absolute; left: 319px; top: 21px;
    display: flex; align-items: center; gap: 10px;
    font-size: 12px; font-weight: 400;
  }
  .contents-label::before {
    content: ""; width: 58px; height: 1px; background: var(--white);
  }

  .toc {
    position: absolute; left: 320px; top: 82px;
    list-style: none;
    display: flex; flex-direction: column; gap: 12.3px;
  }
  .toc li { font-size: 9.3px; line-height: 11px; font-weight: 400; }
  .toc .toc__num { display: block; color: var(--yellow); font-size: 7.5px; font-weight: 500; }
  .toc small { font-size: 7px; }

  .book-title {
    position: absolute; left: 59px; top: 180px;
    font-size: 46px; font-weight: 600; line-height: 47px;
    letter-spacing: -0.01em;
  }
  .chapter-title {
    position: absolute; top: 193px;
    font-size: 31px; font-weight: 500; line-height: 37px;
  }
  .chapter-title__num { color: var(--yellow); display: block; }
  .panel--chapter4 .chapter-title { left: 58px; }
  .panel--chapter9 .chapter-title { left: 52px; }

  .tagline {
    position: absolute; top: 486px;
    font-size: 5.8px; font-weight: 600; letter-spacing: 0.04em;
  }
  .panel--overview .signature--footer, .panel--chapter9 .signature--footer { left: 59px; }
  .panel--overview .tagline, .panel--chapter9 .tagline { left: 96px; }
  .panel--chapter4 .signature--footer { left: 62px; }
  .panel--chapter4 .tagline { left: 95px; }

  .register-tabs { position: absolute; left: 440px; top: 0; width: 58px; height: 521px; }
  .register-tabs text { font-family: "Lexend", sans-serif; font-size: 11px; font-weight: 500; fill: var(--yellow); }
</style>
</head>
<body>

<section class="panel panel--cover">
  <div class="cover-pattern" role="img" aria-label="Dekoratives Linienmuster in dunklerem Rot"></div>
  <div class="brand brand--large">tervalon</div>
  <div class="signature signature--cover" role="img" aria-label="Handschriftliche Unterschrift Konrad Wilmeth"></div>
  <h1 class="cover-title">Experte für<br>Haftungs–<br>fragen</h1>
  <div class="author-vertical">Konrad Wilmeth</div>
  <div class="badge">
    <span class="badge__title">NOTFALL–<br>HANDBUCH</span>
    <span class="badge__sub">FÜR UNTERNEHMER</span>
  </div>
</section>

<section class="panel panel--overview">
  <div class="brand brand--small">tervalon</div>
  <div class="contents-label">Inhalt</div>
  <h2 class="book-title">Notfall–<br>handbuch<br>für Unter–<br>nehmer</h2>
  <ol class="toc">
    <li><span class="toc__num">Kapitel 1 –</span>Einstieg</li>
    <li><span class="toc__num">Kapitel 2 –</span>Organisationshilfen<br>für den Adressaten</li>
    <li><span class="toc__num">Kapitel 3 –</span>Wiedervorlage</li>
    <li><span class="toc__num">Kapitel 4 –</span>Vertretungsplan</li>
    <li><span class="toc__num">Kapitel 5 –</span>Vollmachten</li>
    <li><span class="toc__num">Kapitel 6 –</span>Vermögensstatus</li>
    <li><span class="toc__num">Kapitel 7 –</span>Vorsorgeplan <small>(privat)</small><br>Vorsorgeplan <small>(betrieblich)</small><br>Verfügungen</li>
    <li><span class="toc__num">Kapitel 8 –</span>Wichtige betriebliche<br>Informationen</li>
    <li><span class="toc__num">Kapitel 9 –</span>Risikoanalyse/<br>Unternehmens–Exposé</li>
    <li><span class="toc__num">Kapitel 10 –</span>Weitere Unterlagen</li>
    <li><span class="toc__num">Kapitel 11 –</span>Cyber Security</li>
  </ol>
  <div class="signature signature--footer" role="img" aria-label="Kleine Unterschrift Konrad Wilmeth"></div>
  <div class="tagline">EXPERTE FÜR HAFTUNGSFRAGEN</div>
  <svg class="register-tabs" viewBox="0 0 58 521" aria-hidden="true">
    <defs>
      <filter id="tabShadowA" x="-50%" y="-50%" width="200%" height="200%"><feDropShadow dx="-2" dy="2" stdDeviation="2" flood-opacity="0.3"/></filter>
    </defs>
    <g filter="url(#tabShadowA)" fill="#d94f2b">
      <path d="M6 521 V482 Q6 472 18 470 H58 V521Z"/>
      <path d="M6 470 V437 Q6 427 18 425 H58 V470Z"/>
      <path d="M6 425 V392 Q6 382 18 380 H58 V425Z"/>
      <path d="M6 380 V347 Q6 337 18 335 H58 V380Z"/>
      <path d="M6 335 V302 Q6 292 18 290 H58 V335Z"/>
      <path d="M6 290 V257 Q6 247 18 245 H58 V290Z"/>
      <path d="M6 245 V212 Q6 202 18 200 H58 V245Z"/>
      <path d="M6 200 V167 Q6 157 18 155 H58 V200Z"/>
      <path d="M6 155 V122 Q6 112 18 110 H58 V155Z"/>
      <path d="M6 110 V77 Q6 67 18 65 H58 V110Z"/>
    </g>
    <g fill="none" stroke="#f5c842" stroke-width="1.3">
      <circle cx="33" cy="44" r="11"/><circle cx="33" cy="89" r="11"/><circle cx="33" cy="134" r="11"/>
      <circle cx="33" cy="179" r="11"/><circle cx="33" cy="224" r="11"/><circle cx="33" cy="269" r="11"/>
      <circle cx="33" cy="314" r="11"/><circle cx="33" cy="359" r="11"/><circle cx="33" cy="404" r="11"/>
      <circle cx="33" cy="449" r="11"/><circle cx="33" cy="494" r="11"/>
    </g>
    <g text-anchor="middle">
      <text x="33" y="48">1</text><text x="33" y="93">2</text><text x="33" y="138">3</text>
      <text x="33" y="183">4</text><text x="33" y="228">5</text><text x="33" y="273">6</text>
      <text x="33" y="318">7</text><text x="33" y="363">8</text><text x="33" y="408">9</text>
      <text x="33" y="453">10</text><text x="33" y="498">11</text>
    </g>
  </svg>
</section>

<section class="panel panel--chapter4">
  <div class="brand brand--small">tervalon</div>
  <div class="contents-label">Inhalt</div>
  <h2 class="chapter-title"><span class="chapter-title__num">Kapitel 4 —</span>Vertretungs–<br>plan</h2>
  <ol class="toc">
    <li><span class="toc__num">Kapitel 1 –</span>Einstieg</li>
    <li><span class="toc__num">Kapitel 2 –</span>Organisationshilfen<br>für den Adressaten</li>
    <li><span class="toc__num">Kapitel 3 –</span>Wiedervorlage</li>
    <li><span class="toc__num">Kapitel 4 –</span>Vertretungsplan</li>
    <li><span class="toc__num">Kapitel 5 –</span>Vollmachten</li>
    <li><span class="toc__num">Kapitel 6 –</span>Vermögensstatus</li>
    <li><span class="toc__num">Kapitel 7 –</span>Vorsorgeplan <small>(privat)</small><br>Vorsorgeplan <small>(betrieblich)</small><br>Verfügungen</li>
    <li><span class="toc__num">Kapitel 8 –</span>Wichtige betriebliche<br>Informationen</li>
    <li><span class="toc__num">Kapitel 9 –</span>Risikoanalyse/<br>Unternehmens–Exposé</li>
    <li><span class="toc__num">Kapitel 10 –</span>Weitere Unterlagen</li>
    <li><span class="toc__num">Kapitel 11 –</span>Cyber Security</li>
  </ol>
  <div class="signature signature--footer" role="img" aria-label="Kleine Unterschrift Konrad Wilmeth"></div>
  <div class="tagline">EXPERTE FÜR HAFTUNGSFRAGEN</div>
  <svg class="register-tabs" viewBox="0 0 58 521" aria-hidden="true">
    <defs>
      <filter id="tabShadowB" x="-50%" y="-50%" width="200%" height="200%"><feDropShadow dx="-2" dy="2" stdDeviation="2" flood-opacity="0.3"/></filter>
    </defs>
    <g filter="url(#tabShadowB)" fill="#d94f2b">
      <path d="M6 521 V482 Q6 472 18 470 H58 V521Z"/>
      <path d="M6 470 V437 Q6 427 18 425 H58 V470Z"/>
      <path d="M6 425 V392 Q6 382 18 380 H58 V425Z"/>
      <path d="M6 380 V347 Q6 337 18 335 H58 V380Z"/>
      <path d="M6 335 V302 Q6 292 18 290 H58 V335Z"/>
      <path d="M6 290 V257 Q6 247 18 245 H58 V290Z"/>
      <path d="M6 245 V212 Q6 202 18 200 H58 V245Z"/>
    </g>
    <g fill="none" stroke="#f5c842" stroke-width="1.3">
      <circle cx="33" cy="179" r="11"/><circle cx="33" cy="224" r="11"/><circle cx="33" cy="269" r="11"/>
      <circle cx="33" cy="314" r="11"/><circle cx="33" cy="359" r="11"/><circle cx="33" cy="404" r="11"/>
      <circle cx="33" cy="449" r="11"/><circle cx="33" cy="494" r="11"/>
    </g>
    <g text-anchor="middle">
      <text x="33" y="183">4</text><text x="33" y="228">5</text><text x="33" y="273">6</text>
      <text x="33" y="318">7</text><text x="33" y="363">8</text><text x="33" y="408">9</text>
      <text x="33" y="453">10</text><text x="33" y="498">11</text>
    </g>
  </svg>
</section>

<section class="panel panel--chapter9">
  <div class="brand brand--small">tervalon</div>
  <div class="contents-label">Inhalt</div>
  <h2 class="chapter-title"><span class="chapter-title__num">Kapitel 9 —</span>Risikoanalyse/<br>Unternehmens–<br>Exposé</h2>
  <ol class="toc">
    <li><span class="toc__num">Kapitel 1 –</span>Einstieg</li>
    <li><span class="toc__num">Kapitel 2 –</span>Organisationshilfen<br>für den Adressaten</li>
    <li><span class="toc__num">Kapitel 3 –</span>Wiedervorlage</li>
    <li><span class="toc__num">Kapitel 4 –</span>Vertretungsplan</li>
    <li><span class="toc__num">Kapitel 5 –</span>Vollmachten</li>
    <li><span class="toc__num">Kapitel 6 –</span>Vermögensstatus</li>
    <li><span class="toc__num">Kapitel 7 –</span>Vorsorgeplan <small>(privat)</small><br>Vorsorgeplan <small>(betrieblich)</small><br>Verfügungen</li>
    <li><span class="toc__num">Kapitel 8 –</span>Wichtige betriebliche<br>Informationen</li>
    <li><span class="toc__num">Kapitel 9 –</span>Risikoanalyse/<br>Unternehmens–Exposé</li>
    <li><span class="toc__num">Kapitel 10 –</span>Weitere Unterlagen</li>
    <li><span class="toc__num">Kapitel 11 –</span>Cyber Security</li>
  </ol>
  <div class="signature signature--footer" role="img" aria-label="Kleine Unterschrift Konrad Wilmeth"></div>
  <div class="tagline">EXPERTE FÜR HAFTUNGSFRAGEN</div>
  <svg class="register-tabs" viewBox="0 0 58 521" aria-hidden="true">
    <defs>
      <filter id="tabShadowC" x="-50%" y="-50%" width="200%" height="200%"><feDropShadow dx="-2" dy="2" stdDeviation="2" flood-opacity="0.3"/></filter>
    </defs>
    <g filter="url(#tabShadowC)" fill="#d94f2b">
      <path d="M6 521 V482 Q6 472 18 470 H58 V521Z"/>
      <path d="M6 470 V437 Q6 427 18 425 H58 V470Z"/>
    </g>
    <g fill="none" stroke="#f5c842" stroke-width="1.3">
      <circle cx="33" cy="404" r="11"/><circle cx="33" cy="449" r="11"/><circle cx="33" cy="494" r="11"/>
    </g>
    <g text-anchor="middle">
      <text x="33" y="408">9</text><text x="33" y="453">10</text><text x="33" y="498">11</text>
    </g>
  </svg>
</section>

</body>
</html>
```